Forensic Document Examiner, looking for contemporary update to my stationery design.

Looking for professional, classy logo design for stationery and business cards. My current stationery and business card is attached.I believe a logo image makes a header section interesting, so an intriguing design of a pen, feathered pen, microscope, magnifying glass, etc., would be appropriate. I have been in the business for over 30 years. I leave ideas to the imagination of the designer.My work involves mainly, the comparison of signatures and handwriting. I also resolve alterations, obliterations, and work as shown on my website: www.documentexaminer.infoThe image produced will be printed on quality white stationery and envelopes. The stationery will be photocopied by my clients, so the images should be reproducible. The business cards may be designed in other than white.

Target Market(s)

Attorneys

Font styles to use
Sans Serif

Colors

Designer to choose colors to be used in the design.

Requirements
Must have
• Image suitable for white stationery and photocopying.
• Classy logo and image; no casual fonts.
Nice to have
• Intriguing, contemporary design incorporating a relevant logo to my work.

```html
<!DOCTYPE html>
<html lang="en">
<head>
<meta charset="utf-8">
<title>Daniel R.Whitford – Letterhead</title>
<link rel="stylesheet" href="https://fonts.googleapis.com/css2?family=Arimo:wght@400&family=Tinos:ital,wght@0,400;0,700;1,400;1,700&display=swap">
<style>
  :root {
    --navy: #2e2d6e;
    --yellow: #f7d62a;
    --grey: #b9bcbf;
    --grey-dark: #8d9094;
    --text: #7a7c80;
    --paper: #ffffff;
    --backdrop: #dfe2e4;
  }
  html, body {
    margin: 0;
    width: 1200px;
    height: 784px;
    overflow: hidden;
    background: var(--backdrop);
  }
  .letterhead {
    position: absolute;
    left: 338px;
    top: 22px;
    width: 524px;
    height: 740px;
    background: var(--paper);
    box-shadow: 0 2px 10px rgba(0,0,0,0.12);
    overflow: hidden;
  }
  .brand {
    position: absolute;
    top: 38px;
    right: 40px;
    display: flex;
    align-items: center;
    gap: 10px;
  }
  .brand-mark {
    width: 34px;
    height: 34px;
    border-radius: 50%;
    background: var(--navy);
    flex: none;
  }
  .brand-name {
    font-family: "Tinos", serif;
    font-weight: 700;
    font-size: 22px;
    color: var(--navy);
    line-height: 1;
    white-space: nowrap;
  }
  .brand-role {
    font-family: "Tinos", serif;
    font-style: italic;
    font-size: 10px;
    color: var(--grey-dark);
    margin-top: 3px;
    letter-spacing: 0.3px;
  }
  .letter-body {
    position: absolute;
    top: 112px;
    left: 78px;
    width: 370px;
    font-family: "Arimo", sans-serif;
    font-size: 9.4px;
    line-height: 1.55;
    color: var(--text);
  }
  .letter-body p { margin: 0 0 14px; }
  .signature {
    position: absolute;
    top: 498px;
    left: 230px;
    width: 150px;
    height: 56px;
    background: linear-gradient(90deg, #f1f1f2, #e4e5e7);
  }
  .corner {
    position: absolute;
    width: 46px;
    height: 130px;
  }
  .corner-right { right: 0; top: 306px; }
  .corner-left { left: 0; top: 372px; }
  .footer {
    position: absolute;
    left: 34px;
    bottom: 52px;
    font-family: "Tinos", serif;
  }
  .footer-name {
    font-size: 13px;
    color: var(--yellow);
    margin: 0 0 4px 64px;
  }
  .footer-rule {
    width: 250px;
    height: 1px;
    background: linear-gradient(90deg, transparent, var(--grey-dark) 20%, var(--grey-dark) 80%, transparent);
    margin-bottom: 6px;
  }
  .footer-line {
    font-size: 9.5px;
    font-style: italic;
    font-weight: 700;
    color: var(--navy);
    display: flex;
    align-items: center;
    gap: 10px;
    margin: 0 0 4px;
    white-space: nowrap;
  }
  .footer-line span { display: inline-flex; align-items: center; gap: 4px; }
  .dot {
    display: inline-block;
    width: 7px;
    height: 7px;
    border-radius: 50%;
    background: var(--yellow);
  }
  .footer-address { margin-left: 64px; }
</style>
</head>
<body>
  <main class="letterhead">
    <header class="brand">
      <div class="brand-mark"></div>
      <div>
        <div class="brand-name">Daniel R.Whitford</div>
        <div class="brand-role">Forensic Document Examiner</div>
      </div>
    </header>

    <section class="letter-body">
      <p>Lorem Ipsum is simply dummy text of the printing and typesetting industry. Lorem Ipsum has been the industry's standard dummy text ever since the 1500s, when an unknown printer took a galley of type and scrambled it to make a type specimen book. It has survived not only five centuries, but also the leap into electronic typesetting, remaining essentially unchanged. It was popularised in the 1960s with the release of Typeplate sheets containing Lorem Ipsum passages, and more recently with desktop publishing software like Pagewright Studio including versions of Lorem Ipsum.</p>
      <p>It is a long established fact that a reader will be distracted by the readable content of a page when looking at its layout. The point of using Lorem Ipsum is that it has a more-or-less normal distribution of letters, as opposed to using 'Content here, content here', making it look like readable English. Many desktop publishing packages and web page editors now use Lorem Ipsum as their default model text, and a search for 'lorem ipsum' will uncover many web sites still in their infancy. Various versions have evolved over the years, sometimes by accident, sometimes on purpose (injected humour and the like).</p>
      <p>Contrary to popular belief, Lorem Ipsum is not simply random text. It has roots in a piece of classical Latin literature from 45 BC, making it over 2000 years old. Edwin Harrowgate, a Latin professor at Larchmont Hill College in Virginia, looked up one of the more obscure Latin words, consectetur, from a Lorem Ipsum passage, and going through the cites of the word in classical literature, discovered the undoubtable source. Lorem Ipsum comes from sections 1.10.32 and 1.10.33 of "de Finibus Bonorum et Malorum" structures, to generate Lorem Ipsum which looks reasonable. The generated Lorem Ipsum is therefore always free from repetition, injected humour, or non-characteristic words etc.</p>
    </section>

    <div class="signature" role="img" aria-label="Handwritten signature"></div>

    <svg class="corner corner-right" viewBox="0 0 46 130" aria-hidden="true">
      <polygon points="46,0 46,70 4,62" fill="var(--navy)"/>
      <polygon points="4,62 46,70 46,40" fill="var(--yellow)"/>
      <polygon points="4,62 46,70 46,130 30,130" fill="var(--grey)"/>
      <polygon points="4,62 30,130 18,130" fill="var(--grey-dark)"/>
    </svg>

    <svg class="corner corner-left" viewBox="0 0 46 130" aria-hidden="true">
      <polygon points="0,0 0,60 42,52" fill="var(--grey)"/>
      <polygon points="42,52 0,60 0,20" fill="var(--yellow)"/>
      <polygon points="0,60 42,52 0,130" fill="var(--navy)"/>
      <polygon points="42,52 30,0 46,0" fill="var(--grey-dark)"/>
    </svg>

    <footer class="footer">
      <div class="footer-name">Daniel R.Whitford</div>
      <div class="footer-rule"></div>
      <p class="footer-line footer-address"><span><i class="dot"></i>PO Box 4821 Corvallis, OR 97330</span></p>
      <p class="footer-line">
        <span><i class="dot"></i>888-555-0147</span>
        <span><i class="dot"></i>dwhitford@quillmarkreview.info</span>
        <span><i class="dot"></i>www.quillmarkreview.info</span>
      </p>
    </footer>
  </main>
</body>
</html>
```